Business Cards for IT Consulting Company (Managed Service Provider)

I am looking to have some business cards printed and would like some designs. We are an IT Consulting company based in Vancouver BC. I would like a nice clean and modern look to the cards. I have uploaded all the versions of my logo so parts can be used as needed. Here is a snippit from our website homepage:

Quillbrook Networks Ltd. is an IT Solutions Partner located in Vancouver BC, Canada. We offer IT solutions and support to customers in the greater Vancouver Area. With expertise in Microsoft platforms, as well as Linux and Mac OSX and over 12 years experience in the IT industry, Quillbrook Networks is dedicated to offering our clients top quality service and products. We take pride in the solutions we offer our customers. The greatest compliment a client can give us is to recommend our services.

Quillbrook Networks Ltd. offers a wide range of IT services from onsite service to remote support and managed service solutions. This allows clients to choose the support path that best suits their company’s needs. Supporting many different sized companies from small to enterprise level over the past 12 years Quillbrook Networks has the experience and expertise needed to ensure things run smoothly. Allowing our clients to focus on doing business.

Revolutionizing the way IT services are delivered.

Quillbrook Networks is dedicated to providing our clients with IT solutions that work and grow with them for years to come. This philosophy helps save money in the long run instead of replacing equipment constantly. Far too often IT solutions are not well thought out and while possibly solving the problem at hand, require replacement due to growth or quality within a very short time frame. Quillbrook Networks takes pride in providing solutions that will last and be able to accommodate growth without the need for replacement.

Industry/Entity Type

Information Technology

Contact Information for Business Card

Quillbrook Networks Ltd.
(Employee Name)
Eml: (Employees Email Address)
Web: quillbrook.me
Ph: 604-555-0148

Font styles to use
Serif
Sans Serif

Requirements
Must have
• The Company logo and company colors.
Nice to have
• - Our tag line: "Revolutionizing IT Services" or "Revolutionizing the way IT services are delivered."
• - Also I really like the idea of nature and technology together blending which is sort of where my logo came from so integrating that somehow onto the business cards would be great.

```html
<!DOCTYPE html>
<html lang="en">
<head>
<meta charset="utf-8">
<title>Quillbrook Networks Ltd. – Business Cards</title>
<link rel="stylesheet" href="https://fonts.googleapis.com/css2?family=Open+Sans:wght@400;600;700&display=swap">
<style>
  :root {
    --bg: #2e2a28;
    --paper: #fbfbfb;
    --slate: #636466;
    --blue: #1ba1e2;
    --ink: #58595b;
    --white: #ffffff;
  }
  * { box-sizing: border-box; margin: 0; padding: 0; }
  html, body {
    width: 1200px; height: 844px; overflow: hidden;
    background: var(--bg);
    font-family: "Open Sans", Arial, sans-serif;
  }
  .stage { position: relative; width: 1200px; height: 844px; }
  .card {
    position: absolute; top: 268px;
    width: 540px; height: 309px;
    box-shadow: 0 10px 30px rgba(0,0,0,.45);
  }

  /* Shared wordmark */
  .wordmark {
    position: absolute; left: 0; right: 0;
    display: flex; align-items: center; justify-content: center; gap: 12px;
    color: var(--blue); font-weight: 600; font-size: 25px; letter-spacing: .2px;
  }
  .wordmark__square {
    width: 20px; height: 20px; border: 2px solid var(--blue);
  }

  /* Front */
  .card--front { left: 45px; background: var(--paper); }
  .card--front .wordmark { top: 78px; }
  .name-row {
    position: absolute; left: 0; right: 0; top: 190px;
    display: flex; align-items: center; gap: 10px;
  }
  .name-row__rule { height: 1px; background: var(--blue); }
  .name-row__rule--left { width: 22px; }
  .name-row__rule--right { flex: 1; }
  .name { font-size: 19px; font-weight: 700; white-space: nowrap; }
  .name__first { color: var(--blue); }
  .name__last { color: var(--ink); }
  .contacts {
    position: absolute; left: 32px; top: 228px;
    list-style: none; color: var(--ink); font-size: 14px; line-height: 22px;
  }
  .contacts li { display: flex; align-items: center; gap: 9px; }
  .contacts svg { width: 11px; height: 11px; fill: var(--blue); flex: none; }

  /* Back */
  .card--back { left: 615px; background: var(--slate); }
  .card--back .wordmark { top: 96px; }
  .tagline-band {
    position: absolute; left: 0; right: 0; top: 212px; height: 50px;
    background: var(--white);
    display: flex; align-items: center; justify-content: center;
    color: var(--blue); font-weight: 600; font-size: 15px;
  }
</style>
</head>
<body>
<main class="stage">

  <section class="card card--front" aria-label="Business card front">
    <div class="wordmark">
      <span class="wordmark__square"></span>
      <span class="wordmark__name">Quillbrook Networks Ltd.</span>
    </div>
    <div class="name-row">
      <span class="name-row__rule name-row__rule--left"></span>
      <span class="name"><span class="name__first">Daniel</span> <span class="name__last">Harper</span></span>
      <span class="name-row__rule name-row__rule--right"></span>
    </div>
    <ul class="contacts">
      <li>
        <svg viewBox="0 0 24 24" aria-hidden="true"><path d="M6.6 10.8a15.1 15.1 0 0 0 6.6 6.6l2.2-2.2c.3-.3.7-.4 1-.2 1.1.4 2.3.6 3.6.6.6 0 1 .4 1 1V20c0 .6-.4 1-1 1A17 17 0 0 1 3 4c0-.6.4-1 1-1h3.5c.6 0 1 .4 1 1 0 1.3.2 2.5.6 3.6.1.3 0 .7-.2 1z"/></svg>
        <span>604-555-0148</span>
      </li>
      <li>
        <svg viewBox="0 0 24 24" aria-hidden="true"><path d="M2 5h20v14H2zm2 2v.5l8 5 8-5V7z"/></svg>
        <span>info@quillbrook.me</span>
      </li>
      <li>
        <svg viewBox="0 0 24 24" aria-hidden="true"><circle cx="12" cy="12" r="10"/></svg>
        <span>www.quillbrook.me</span>
      </li>
    </ul>
  </section>

  <section class="card card--back" aria-label="Business card back">
    <div class="wordmark">
      <span class="wordmark__square"></span>
      <span class="wordmark__name">Quillbrook Networks Ltd.</span>
    </div>
    <div class="tagline-band">Revolutionizing IT Services</div>
  </section>

</main>
</body>
</html>
```